Business Card - high end, modern health care

Hey designers!

We need a double sided business card for the boutique, cutting edge physical therapy rehabilitation centre in Sydney's Northern Beaches.

With the most qualified physios in the area The Harbourview Motion Clinic does what other physiotherapy practices do not, we take our time with our patients giving them longer appointments, better physios and therefor faster results!

We guarantee that the service people receive at THMC will be unparalleled.

Hence we need a business card to reflect our modern, boutique, high end service. The final design needs to reflect that we are in a class of our own yet with the feel of beachside retreat.

Below I have attached our logo in both blue on white and white on blue. The exact colour is;
and the font that we have used in our logo is Tex Gyre Aventador.

I like the idea of the blue as the main colour as it is more eye catching and our signage onto the main road will be in this blue and in the interest of consistency across marketing the blue needs to be a part of the design. However I would appreciate a few designs onto a wooden background as this is a visual theme within the fitout of the practice.

The design needs to be of standard size (91x55mm).

Target Market(s)

We target people who have an end outcome in mind and those who have had poor experiences with other providers and ensure that everyone gets the care that they deserve with a premium service that is tailored to the individuals circumstances. As a premium service, the target market is highly educated, business and tech savvy with the additional target market of elderly people who have self funded their retirement and see value in paying for the best ongoing rehabilitation to maintain independence.

Industry/Entity Type

Physical Therapy

Contact Information for Business Card

Name, designation( Titled Musculoskeletal Physiotherapist... there will also be those in the company that have multiple designations ie 5 or 6 words long), phone number, email, facebook, instagram, address

Font styles to use
Sans Serif

Colors

Designer to choose colors to be used in the design.

Requirements
Must have
• Front - The logo as large as possible, blue or wooden theme, and all of the important details.
• Back - A blank space/lines on which to write appointment times (no "Appointment, date, time" etc.)
Nice to have
• facebook url
• logos for facebook and instagram
• Mini logos for the phone and email?

```html
<!DOCTYPE html>
<html lang="en">
<head>
<meta charset="utf-8">
<title>The Harbourview Motion Clinic – Business Card</title>
<link rel="stylesheet" href="https://fonts.googleapis.com/css2?family=Montserrat:wght@400;500;700&display=swap">
<style>
  :root {
    --brand-blue: #0f57ad;
    --paper: #ffffff;
    --rule: #6f7680;
    --backdrop: #e9eaec;
  }
  * { margin: 0; padding: 0; box-sizing: border-box; }
  html, body { width: 1200px; height: 930px; overflow: hidden; }
  body {
    background: var(--backdrop);
    font-family: "Montserrat", sans-serif;
    position: relative;
  }
  .card {
    position: absolute;
    width: 640px;
    height: 387px;
    border-radius: 18px;
    overflow: hidden;
    background: var(--paper);
    box-shadow: 0 6px 18px rgba(0,0,0,0.12);
  }
  .card--back { left: 110px; top: 50px; }
  .card--front { left: 450px; top: 493px; }

  /* shared brand lockup */
  .brand { position: absolute; display: flex; align-items: center; gap: 12px; }
  .brand__dot { width: 46px; height: 46px; border-radius: 50%; flex: none; }
  .brand__name {
    font-weight: 700;
    font-size: 21px;
    line-height: 1.15;
    letter-spacing: 0.02em;
    text-transform: uppercase;
  }

  /* back side */
  .back__band {
    position: absolute; left: 0; top: 0; width: 100%; height: 170px;
    background: var(--brand-blue);
  }
  .card--back .brand { left: 150px; top: 56px; }
  .card--back .brand__dot { background: var(--paper); }
  .card--back .brand__name { color: var(--paper); }
  .back__label {
    position: absolute; left: 0; top: 186px; width: 100%;
    text-align: center;
    color: var(--brand-blue);
    font-size: 15px; font-weight: 500;
    letter-spacing: 0.03em;
  }
  .back__lines { position: absolute; left: 80px; right: 80px; top: 232px; }
  .back__line { height: 1px; background: var(--rule); margin-bottom: 44px; }

  /* front side */
  .front__shape { position: absolute; inset: 0; }
  .card--front .brand { left: 290px; top: 58px; }
  .card--front .brand__dot { background: var(--brand-blue); }
  .card--front .brand__name { color: var(--brand-blue); }

  .contact {
    position: absolute; left: 42px; bottom: 34px;
    color: var(--paper);
  }
  .contact__name { font-weight: 700; font-size: 22px; letter-spacing: 0.01em; text-transform: uppercase; }
  .contact__role { font-size: 14px; margin-top: 2px; }
  .contact__address { font-size: 14px; line-height: 1.45; margin-top: 14px; }
  .contact__list { list-style: none; margin-top: 10px; font-size: 14px; line-height: 1.55; }
  .contact__list li { display: flex; align-items: center; gap: 10px; }
  .contact__icon { width: 13px; height: 13px; flex: none; }
</style>
</head>
<body>

<section class="card card--back" aria-label="Card back – appointment side">
  <div class="back__band"></div>
  <div class="brand">
    <span class="brand__dot"></span>
    <span class="brand__name">The Harbourview<br>Motion Clinic</span>
  </div>
  <p class="back__label">Appointment</p>
  <div class="back__lines">
    <div class="back__line"></div>
    <div class="back__line"></div>
    <div class="back__line"></div>
  </div>
</section>

<section class="card card--front" aria-label="Card front – contact side">
  <svg class="front__shape" width="640" height="387" viewBox="0 0 640 387" aria-hidden="true">
    <path d="M0,0 L236,0 Q306,322 640,322 L640,387 L0,387 Z" fill="var(--brand-blue)"/>
    <path d="M222,0 Q292,336 640,336" fill="none" stroke="var(--paper)" stroke-width="3"/>
  </svg>

  <div class="brand">
    <span class="brand__dot"></span>
    <span class="brand__name">The Harbourview<br>Motion Clinic</span>
  </div>

  <div class="contact">
    <p class="contact__name">Daniel Whitford</p>
    <p class="contact__role">Director</p>
    <p class="contact__address">24 Sample Street, Unit 1,<br>Town Name, PO 12345</p>
    <ul class="contact__list">
      <li>
        <svg class="contact__icon" viewBox="0 0 16 16" aria-hidden="true"><path d="M3.5 1.5l2.6 2.8-1.4 2a8 8 0 0 0 5 5l2-1.4 2.8 2.6-1.6 2A11 11 0 0 1 1.5 3.1z" fill="#fff"/></svg>
        +61 2 5550 4127
      </li>
      <li>
        <svg class="contact__icon" viewBox="0 0 16 16" aria-hidden="true"><rect x="1.5" y="3.5" width="13" height="9" fill="none" stroke="#fff" stroke-width="1.6"/><path d="M1.5 3.5L8 9l6.5-5.5" fill="none" stroke="#fff" stroke-width="1.6"/></svg>
        info@harbourviewmotion.com
      </li>
      <li>
        <svg class="contact__icon" viewBox="0 0 16 16" aria-hidden="true"><circle cx="8" cy="8" r="6.5" fill="none" stroke="#fff" stroke-width="1.5"/><ellipse cx="8" cy="8" rx="3" ry="6.5" fill="none" stroke="#fff" stroke-width="1.2"/><path d="M1.5 8h13" stroke="#fff" stroke-width="1.2"/></svg>
        www.harbourviewmotion.com
      </li>
    </ul>
  </div>
</section>

</body>
</html>
```